Existing Website Requiring new Pages

I have an existing word press website that was built using elementor.
Website: www.tallowcrestcare.com.au
I require the Vacancies page (https://www.tallowcrestcare.com.au/vacancies/) to be modified to display our new properties along with minor tweaks to how the information is presented.
The vacancies to be displayed are the exactly the same as those that are located on the homepage of QMR website (https://qmr.org.au/)
The new pages that link off the Vacancies tab will require custom design.
There are roughly 8 pages/properties to be incorporated. i wish for the design to be very similar to that displayed in the following link; https://www.polunda.com.au/vacancies/merrylands
Along with this the back end has not been updated for the last 3 years so it also requires some maintenance.
Website is in the disability industry and the custom pages will display information relative to Property Vacancies.
I have attached a ZIP file with some design guides, the information for each of the properties (which will need to be modified to show our business name Tallowcrest Care) and the example of how it is to look based off the Polunda website.
If you guys have any suggestions or ideas on how to make this more presentable or possible i'm open to your ideas.
Target Market(s)
People looking for SDA properties custom built for people with a disability
Industry/Entity Type
Disability
Coding
Coded - Design and coding required
Number of Pages Required
5+ page

```html
<!DOCTYPE html>
<html lang="en">
<head>
<meta charset="utf-8">
<title>Vacancies – Tallowcrest Care</title>
<link href="https://fonts.googleapis.com/css2?family=Montserrat:wght@400;500;600;700&display=swap" rel="stylesheet">
<style>
:root{
  --yellow:#fdcb6f;
  --pink:#f46fb2;
  --pink-bar:#fb74b8;
  --teal:#18c39c;
  --ink:#1c1c1c;
  --nav:#3a3a3a;
  --body:#555;
  --muted:#8a8a8a;
  --line:#e4e4e4;
  --blue:#2a8fd8;
  --footer:#fbfbfb;
  --bar:#1d1d1d;
}
*{box-sizing:border-box;margin:0;padding:0}
html,body{width:769px;height:1200px;overflow:hidden;background:#fff}
body{position:relative;font-family:'Montserrat',sans-serif;color:var(--ink)}

.site-header{position:absolute;left:0;top:0;width:769px;height:96px;background:#fff}
.brand{position:absolute;left:71px;top:30px;display:flex;align-items:center;gap:6px}
.brand-dot{width:18px;height:18px;border-radius:50%;background:var(--pink)}
.brand-name{font-weight:600;font-size:11px;color:var(--ink);letter-spacing:.3px}
.main-nav{position:absolute;right:71px;top:40px;display:flex;gap:17px;font-size:7.4px;font-weight:600;letter-spacing:.5px;color:var(--nav)}
.main-nav .active{color:#f29a5a}

.hero{position:absolute;left:0;top:96px;width:769px;height:247px;background:var(--yellow);overflow:hidden}
.hero svg{position:absolute;left:0;top:0}
.hero-title{position:absolute;left:477px;top:98px;font-size:44px;font-weight:700;color:#fff;letter-spacing:-.5px}

.listings{position:absolute;left:71px;top:377px;display:grid;grid-template-columns:repeat(4,153px);column-gap:4.5px;row-gap:21px}
.card{position:relative;width:153px;height:253px;border:1px solid var(--line);border-radius:4px;background:#fff;overflow:hidden}
.card-photo{height:127px;width:100%}
.fav{position:absolute;right:8px;top:8px;width:12px;height:11px}
.card-title{position:absolute;left:11px;top:138px;font-size:11px;font-weight:700;letter-spacing:.2px}
.card-text{position:absolute;left:12px;top:157px;width:135px;font-size:8.3px;line-height:11.5px;color:var(--body)}
.beds{position:absolute;left:12px;top:193px;display:flex;align-items:center;gap:2px;font-size:8.6px;font-weight:500;color:var(--teal)}
.card-link{position:absolute;left:0;top:219px;width:100%;height:34px;border-top:1px solid var(--line);padding:9px 11px;font-size:9.6px;font-weight:500;color:var(--pink)}
.card-link.is-hover{background:var(--pink-bar);color:#fff;border-top-color:var(--pink-bar)}

.site-footer{position:absolute;left:0;top:940px;width:769px;height:215px;background:linear-gradient(#f2f2f2,var(--footer) 14px)}
.footer-brand{position:absolute;left:71px;top:40px;display:flex;align-items:center;gap:6px}
.contact{position:absolute;left:71px;top:135px;font-size:8.6px;color:var(--body);line-height:16px;list-style:none}
.contact li{display:flex;align-items:center;gap:6px}
.contact svg{flex:none}
.social{position:absolute;left:346px;top:36px;display:flex;flex-direction:column;gap:5px}
.social span{display:block;width:24px;height:24px;border-radius:50%}
.social .badge{width:20px;height:20px;margin-left:2px;background:#6b2d88}
.col{position:absolute;top:30px;width:151px}
.col h4{font-size:10.4px;font-weight:500;border-left:2px solid var(--blue);padding-left:9px;line-height:11px;margin-bottom:6px;letter-spacing:.2px}
.col ul{list-style:none;border-top:1px solid var(--line)}
.col li{font-size:8.6px;line-height:16px;color:var(--muted);border-bottom:1px solid var(--line);padding:4px 0}
.col.accom{left:408px}
.col.services{left:576px}
.col.services li{padding:3px 0 3px}

.bottom-bar{position:absolute;left:0;top:1155px;width:769px;height:45px;background:var(--bar);color:#aaa;font-size:7.4px;text-align:center;line-height:45px}
.to-top{position:absolute;right:6px;top:16px;width:24px;height:24px;background:#2c2c2c;display:flex;align-items:center;justify-content:center}
</style>
</head>
<body>

<header class="site-header">
  <div class="brand"><span class="brand-dot"></span><span class="brand-name">Tallowcrest Care</span></div>
  <nav class="main-nav">
    <span>HOME</span><span>ABOUT US</span><span class="active">WHAT WE DO ▾</span><span>REFERRALS</span><span>FEEDBACK</span><span>CONTACT US</span>
  </nav>
</header>

<section class="hero">
  <svg width="769" height="247" viewBox="0 0 769 247">
    <defs>
      <linearGradient id="heroPhoto" x1="0" y1="0" x2="0.6" y2="1">
        <stop offset="0" stop-color="#f2b45a"/>
        <stop offset=".35" stop-color="#8a5a3c"/>
        <stop offset=".7" stop-color="#5b4a3c"/>
        <stop offset="1" stop-color="#6f9a4c"/>
      </linearGradient>
    </defs>
    <circle cx="176" cy="36" r="248" fill="url(#heroPhoto)" role="img" aria-label="Photo of a person in a wheelchair in front of a large family house at sunset"/>
  </svg>
  <h1 class="hero-title">Vacancies</h1>
</section>

<main class="listings">
  <article class="card">
    <div class="card-photo" role="img" aria-label="Photo of a brick home with a garage" style="background:linear-gradient(#dfe6ef,#b9b4ac 55%,#7f9a5a)"></div>
    <svg class="fav" viewBox="0 0 24 22"><path d="M12 21 2 11a6 6 0 0 1 10-8 6 6 0 0 1 10 8z" fill="#fff"/></svg>
    <h2 class="card-title">PENRITH</h2>
    <p class="card-text">Lorem ipsum doloet, consectur adipiscing elit, sed do eiusmod</p>
    <p class="beds"><svg width="14" height="9" viewBox="0 0 14 9"><path d="M0 0h1.5v5H14v4h-1.5V7.5h-11V9H0z M3 2h2.5v2.5H3z M6.5 2.5H13v2.5H6.5z" fill="#111"/></svg> 4 bed SIL Home</p>
    <span class="card-link">Learn More ›</span>
  </article>
  <article class="card">
    <div class="card-photo" role="img" aria-label="Photo of a brick home with a hedge and paved driveway" style="background:linear-gradient(#b9d8ef,#a8765c 50%,#6e9a3e)"></div>
    <svg class="fav" viewBox="0 0 24 22"><path d="M12 21 2 11a6 6 0 0 1 10-8 6 6 0 0 1 10 8z" fill="#fff"/></svg>
    <h2 class="card-title">MOUNT DRUITT</h2>
    <p class="card-text">Lorem ipsum doloet, consectur adipiscing elit, sed do eiusmod</p>
    <p class="beds"><svg width="14" height="9" viewBox="0 0 14 9"><path d="M0 0h1.5v5H14v4h-1.5V7.5h-11V9H0z M3 2h2.5v2.5H3z M6.5 2.5H13v2.5H6.5z" fill="#111"/></svg> 4 bed SIL Home</p>
    <span class="card-link is-hover">Learn More ›</span>
  </article>
  <article class="card">
    <div class="card-photo" role="img" aria-label="Photo of a cream single-storey home" style="background:linear-gradient(#7cc3ef,#d9cfa6 50%,#7aa44e)"></div>
    <svg class="fav" viewBox="0 0 24 22"><path d="M12 21 2 11a6 6 0 0 1 10-8 6 6 0 0 1 10 8z" fill="#fff"/></svg>
    <h2 class="card-title">CASULA</h2>
    <p class="card-text">Lorem ipsum doloet, consectur adipiscing elit, sed do eiusmod</p>
    <p class="beds"><svg width="14" height="9" viewBox="0 0 14 9"><path d="M0 0h1.5v5H14v4h-1.5V7.5h-11V9H0z M3 2h2.5v2.5H3z M6.5 2.5H13v2.5H6.5z" fill="#111"/></svg> 4 bed SIL Home</p>
    <span class="card-link">Learn More ›</span>
  </article>
  <article class="card">
    <div class="card-photo" role="img" aria-label="Photo of a period cottage with a front lawn" style="background:linear-gradient(#cfe2f0,#e8d6bd 45%,#6fae3f)"></div>
    <svg class="fav" viewBox="0 0 24 22"><path d="M12 21 2 11a6 6 0 0 1 10-8 6 6 0 0 1 10 8z" fill="#fff"/></svg>
    <h2 class="card-title">EASTWOOD</h2>
    <p class="card-text">Lorem ipsum doloet, consectur adipiscing elit, sed do eiusmod</p>
    <p class="beds"><svg width="14" height="9" viewBox="0 0 14 9"><path d="M0 0h1.5v5H14v4h-1.5V7.5h-11V9H0z M3 2h2.5v2.5H3z M6.5 2.5H13v2.5H6.5z" fill="#111"/></svg> 4 bed SIL Home</p>
    <span class="card-link">Learn More ›</span>
  </article>

  <article class="card">
    <div class="card-photo" role="img" aria-label="Photo of a home with palm trees and a green lawn" style="background:linear-gradient(#e6eef5,#c9a88a 45%,#4f9a33)"></div>
    <svg class="fav" viewBox="0 0 24 22"><path d="M12 21 2 11a6 6 0 0 1 10-8 6 6 0 0 1 10 8z" fill="#fff"/></svg>
    <h2 class="card-title">BAULKHAM HILLS</h2>
    <p class="card-text">Lorem ipsum doloet, consectur adipiscing elit, sed do eiusmod</p>
    <p class="beds"><svg width="14" height="9" viewBox="0 0 14 9"><path d="M0 0h1.5v5H14v4h-1.5V7.5h-11V9H0z M3 2h2.5v2.5H3z M6.5 2.5H13v2.5H6.5z" fill="#111"/></svg> 4 bed SIL Home</p>
    <span class="card-link">Learn More ›</span>
  </article>
  <article class="card">
    <div class="card-photo" role="img" aria-label="Photo of an orange brick home with a carport" style="background:linear-gradient(#9fcdef,#c8703e 50%,#8fa86a)"></div>
    <svg class="fav" viewBox="0 0 24 22"><path d="M12 21 2 11a6 6 0 0 1 10-8 6 6 0 0 1 10 8z" fill="#fff"/></svg>
    <h2 class="card-title">MERRYLANDS</h2>
    <p class="card-text">Lorem ipsum doloet, consectur adipiscing elit, sed do eiusmod</p>
    <p class="beds"><svg width="14" height="9" viewBox="0 0 14 9"><path d="M0 0h1.5v5H14v4h-1.5V7.5h-11V9H0z M3 2h2.5v2.5H3z M6.5 2.5H13v2.5H6.5z" fill="#111"/></svg> 4 bed SIL Home</p>
    <span class="card-link">Learn More ›</span>
  </article>
  <article class="card">
    <div class="card-photo" role="img" aria-label="Photo of a two-storey weatherboard home" style="background:linear-gradient(#3bb2f0,#c9cfd6 50%,#6e9d3a)"></div>
    <svg class="fav" viewBox="0 0 24 22"><path d="M12 21 2 11a6 6 0 0 1 10-8 6 6 0 0 1 10 8z" fill="#fff"/></svg>
    <h2 class="card-title">LOREM IPSUM</h2>
    <p class="card-text">Lorem ipsum doloet, consectur adipiscing elit, sed do eiusmod</p>
    <p class="beds"><svg width="14" height="9" viewBox="0 0 14 9"><path d="M0 0h1.5v5H14v4h-1.5V7.5h-11V9H0z M3 2h2.5v2.5H3z M6.5 2.5H13v2.5H6.5z" fill="#111"/></svg> 4 bed SIL Home</p>
    <span class="card-link">Learn More ›</span>
  </article>
  <article class="card">
    <div class="card-photo" role="img" aria-label="Photo of a grey two-storey home with a double garage" style="background:linear-gradient(#b5d7f0,#6f7886 50%,#8f9698)"></div>
    <svg class="fav" viewBox="0 0 24 22"><path d="M12 21 2 11a6 6 0 0 1 10-8 6 6 0 0 1 10 8z" fill="#fff"/></svg>
    <h2 class="card-title">LOREM IPSUM</h2>
    <p class="card-text">Lorem ipsum doloet, consectur adipiscing elit, sed do eiusmod</p>
    <p class="beds"><svg width="14" height="9" viewBox="0 0 14 9"><path d="M0 0h1.5v5H14v4h-1.5V7.5h-11V9H0z M3 2h2.5v2.5H3z M6.5 2.5H13v2.5H6.5z" fill="#111"/></svg> 4 bed SIL Home</p>
    <span class="card-link">Learn More ›</span>
  </article>
</main>

<footer class="site-footer">
  <div class="footer-brand"><span class="brand-dot"></span><span class="brand-name">Tallowcrest Care</span></div>
  <ul class="contact">
    <li><svg width="10" height="8" viewBox="0 0 10 8"><rect x=".5" y=".5" width="9" height="7" fill="none" stroke="#f46fb2"/><path d="M.5.8 5 4.5 9.5.8" fill="none" stroke="#f46fb2"/></svg>Email: info@tallowcrestcare.com.au</li>
    <li><svg width="10" height="10" viewBox="0 0 10 10"><path d="M2 0 4 2.5 3 4q1 2 3 3l1.5-1L10 8 8.5 10Q3 9 0 1.5z" fill="#f46fb2"/></svg>Phone: +61 0412 580 364</li>
    <li><svg width="10" height="10" viewBox="0 0 10 10"><circle cx="5" cy="5" r="4.3" fill="none" stroke="#f46fb2"/><path d="M5 2.5V5l1.8 1.2" fill="none" stroke="#f46fb2"/></svg>Operating Hours: 9AM To 5PM Monday - Friday</li>
  </ul>
  <div class="social">
    <span class="badge"></span>
    <span style="background:#3b5b9a"></span>
    <span style="background:#1c1c1c"></span>
    <span style="background:#1677b5"></span>
  </div>
  <div class="col accom">
    <h4>ACCOMMODATION</h4>
    <ul>
      <li>Supported Independent Living (SIL)</li>
      <li>Specialist Disability Accommodation (SDA)</li>
      <li>Short term Accommodation (Respite)</li>
      <li>Vacancies</li>
    </ul>
  </div>
  <div class="col services">
    <h4>WHAT WE DO</h4>
    <ul>
      <li>In Home Care</li>
      <li>Social &amp; Community Services</li>
      <li>Therapeutic Supports</li>
      <li>Support Coordination</li>
      <li>Home Modifications</li>
    </ul>
  </div>
</footer>

<div class="bottom-bar">
  © Copyright 2021 | Tallowcrest Care | All Rights Reserved.
  <span class="to-top"><svg width="8" height="5" viewBox="0 0 8 5"><path d="M0 5 4 0l4 5z" fill="#fff"/></svg></span>
</div>

</body>
</html>
```